Purpose, Mission, and Values Poster Update

Crestline Field Laboratories, a Testing, Inspection, and Certification company in the Atlanta area, needs an updated PMV poster. Looking to update graphics and presentation, moving away from current design. Want to carry over company logo, colors (you can include additional blues in the design beyond what is mentioned in the brand guidelines as the previous design did), and messaging (see attachments).

We would also like a companion poster, using the same design language, that shows our goals for leads and won opportunities. Want to carry over logo, colors, and messaging from original, except for this one we want the leads goal to be 115 instead of 85.

Both posters need to be 6000w x 7200h at 300ppi, CMYK. We want to move away from the cartoony, corporate clipart sort of look that the current design has, as new leadership doesn't like the aesthetic.

Target Market(s)

Internal - group of engineers, chemists, scientists, and other technical personnel

Industry/Entity Type

TIC (Testing, Inspection, Certification)

Font styles to use
Serif
Sans Serif

Colors
0054AA
0677BA
7BADD7
CADEEF
E8F1F8

Requirements
Must have
• For both: CMYK colors for printing, 6000w x 7200h at 300ppi for poster sizing leads, company logo; for PMV poster: phrasing of purpose, mission, and values statements preserved; for ring the bell poster: leads goal updated to 115, opportunities goal unchanged at 25
Should not have
• Corporate clipart, cartoon characters

```html
<!DOCTYPE html>
<html lang="en">
<head>
<meta charset="utf-8">
<title>Crestline Field Laboratories — Purpose, Mission &amp; Values</title>
<link rel="stylesheet" href="https://fonts.googleapis.com/css2?family=Anton&family=Archivo:wdth,wght@100..125,400;100..125,700&family=Orbitron:wght@600&family=Arimo:wght@400&display=swap">
<style>
  :root {
    --backdrop: #ecebe8;
    --navy: #1c2152;
    --cyan: #3fc4ea;
    --cyan-deep: #37aed6;
    --ice: #cfe4ee;
    --body: #d9e3ea;
    --dot-field: #262c5e;
  }
  * { margin: 0; padding: 0; box-sizing: border-box; }
  html, body {
    width: 1200px; height: 1189px; overflow: hidden;
    background: var(--backdrop);
  }
  .poster {
    position: absolute; left: 130px; top: 30px;
    width: 940px; height: 1128px;
    background: var(--navy);
    overflow: hidden;
  }
  .brand-mark {
    position: absolute; left: 62px; top: 492px;
    width: 140px; height: 140px;
    background: var(--ice);
  }
  .brand-name {
    position: absolute; left: 222px; top: 632px;
    transform: rotate(-90deg); transform-origin: 0 0;
    font-family: "Archivo", sans-serif; font-weight: 400;
    font-size: 38px; line-height: 1; white-space: nowrap;
    color: var(--ice);
    width: 560px;
  }
  .heading {
    position: absolute;
    font-family: "Anton", sans-serif; font-weight: 400;
    color: var(--cyan); line-height: 1; letter-spacing: 0.5px;
  }
  .heading--purpose { left: 337px; top: 66px; font-size: 84px; }
  .heading--mission { left: 333px; top: 286px; font-size: 84px; }
  .heading--values  { left: 328px; top: 556px; font-size: 104px; color: var(--cyan-deep); }
  .statement {
    position: absolute;
    font-family: "Archivo", sans-serif; font-weight: 700;
    font-stretch: 115%;
    color: var(--ice);
  }
  .statement--purpose { left: 337px; top: 176px; font-size: 34px; line-height: 41px; }
  .statement--mission { left: 333px; top: 398px; font-size: 35px; line-height: 42px; }
  .value { position: absolute; width: 270px; }
  .value__title {
    font-family: "Orbitron", sans-serif; font-weight: 600;
    font-size: 27px; line-height: 31px; color: var(--cyan);
    margin-bottom: 14px;
  }
  .value__text {
    font-family: "Arimo", sans-serif; font-size: 16px; line-height: 19px;
    color: var(--body);
  }
  .value--people     { left: 46px;  top: 690px; }
  .value--service    { left: 324px; top: 700px; }
  .value--global     { left: 591px; top: 716px; color: var(--cyan-deep); }
  .value--create     { left: 46px;  top: 895px; }
  .value--right      { left: 324px; top: 912px; }
  .dot-field {
    position: absolute; left: 737px; top: 1053px;
    width: 62px; height: 52px;
    background: var(--dot-field);
  }
</style>
</head>
<body>
  <main class="poster">
    <div class="brand-mark"></div>
    <div class="brand-name">Crestline Field Laboratories</div>

    <h2 class="heading heading--purpose">PURPOSE</h2>
    <p class="statement statement--purpose">Create a Safe and<br>a reliable world</p>

    <h2 class="heading heading--mission">MISSION</h2>
    <p class="statement statement--mission">Deliver assurance through<br>precise technical and<br>professional services</p>

    <h2 class="heading heading--values">OUR VALUES</h2>

    <section class="value value--people">
      <h3 class="value__title">Keep<br>People<br>First</h3>
      <p class="value__text">Foster a collaborative and<br>inclusive environment for<br>team member’s growth</p>
    </section>
    <section class="value value--service">
      <h3 class="value__title">Deliver<br>Service<br>Excellence</h3>
      <p class="value__text">Provide best-in-class<br>experiences for our clients</p>
    </section>
    <section class="value value--global">
      <h3 class="value__title">Think<br>Global, Act<br>Local</h3>
      <p class="value__text">Utilize our combined<br>expertise and knowledge<br>to deliver when and where</p>
    </section>
    <section class="value value--create">
      <h3 class="value__title">Create<br>Values</h3>
      <p class="value__text">Work efficiently and effectively<br>to deliver quality results in<br>complex environments</p>
    </section>
    <section class="value value--right">
      <h3 class="value__title">Do What’s<br>Right</h3>
      <p class="value__text">Hold ourselves accountable to<br>the highest safety, professional<br>and personal standards</p>
    </section>

    <div class="dot-field" role="img" aria-label="Small decorative dot grid accent"></div>
  </main>
</body>
</html>
```